Help design website for "Brightwater Civic Advisors" to advance the common good

Here is the Google doc link that lays out the design:

https://files.plumrivet.example/sheet/d/7QmTzR2wLx9KpVbN4hJcY8sEaUoFdG3iXkMnPq5rWt6/edit?usp=sharing

Here is the Google drive folder with the logos and photos: https://vault.plumrivet.example/open?id=4HkWp9LzQe2TxRvN8mBaYc3DsUoJfG6

The testimonials are being gathered and will be shared by Friday, 1/4.

The winner will also have to migrate the coding files to my hosting site.

Thank you for your help! Looking forward to seeing your designs.

Target Market(s)

Prospective clients

Industry/Entity Type

Non Profit

Coding

Coded - Design and coding required

Number of Pages Required

5+ page

Requirements
Must have
• Noted in the Google doc regarding layout.
Nice to have

```html
<!DOCTYPE html>
<html lang="en">
<head>
<meta charset="utf-8">
<title>Contact – Brightwater Civic Advisors</title>
<link href="https://fonts.googleapis.com/css2?family=Poppins:wght@400;500;600;700&family=Open+Sans:wght@400;600;700&display=swap" rel="stylesheet">
<style>
  :root {
    --brand-blue: #3d8bcd;
    --ink: #111111;
    --body-text: #2a2a2a;
    --field-border: #bdbdbd;
    --footer-dark: #262730;
    --band-light: #f1f1f1;
    --white: #ffffff;
    --muted-line: #4a4b55;
  }
  * { margin: 0; padding: 0; box-sizing: border-box; }
  html, body { width: 1053px; height: 1200px; overflow: hidden; background: var(--white); }
  .page { position: relative; width: 1053px; height: 1200px; overflow: hidden; font-family: "Open Sans", sans-serif; color: var(--body-text); }

  /* Header */
  .site-header { position: absolute; left: 0; top: 0; width: 1053px; height: 124px; background: var(--brand-blue); }
  .brand { position: absolute; display: flex; align-items: center; gap: 12px; font-family: "Poppins", sans-serif; font-weight: 500; color: var(--white); text-transform: uppercase; }
  .brand-mark { width: 14px; height: 14px; background: var(--white); flex: none; }
  .brand-name { line-height: 1.12; }
  .site-header .brand { left: 128px; top: 30px; font-size: 19px; letter-spacing: 6px; }
  .cta-button { position: absolute; left: 646px; top: 34px; width: 281px; height: 36px; border: 2px solid var(--white); color: var(--white); font-family: "Poppins", sans-serif; font-weight: 600; font-size: 12.3px; display: flex; align-items: center; justify-content: center; text-decoration: none; }
  .main-nav { position: absolute; top: 92px; left: 0; font-family: "Poppins", sans-serif; font-weight: 600; font-size: 12.3px; color: var(--white); }
  .main-nav a { position: absolute; white-space: nowrap; color: var(--white); text-decoration: none; }
  .main-nav .is-current { border-bottom: 2px solid var(--white); padding: 0 4px 0 0; }

  /* Content */
  .page-title { position: absolute; top: 166px; width: 100%; text-align: center; font-family: "Poppins", sans-serif; font-weight: 600; font-size: 28px; color: var(--ink); }
  .portrait { position: absolute; left: 88px; top: 252px; width: 150px; height: 150px; border-radius: 50%; border: 4px solid #e4e4e4; background: radial-gradient(circle at 50% 45%, #8a6a58 0%, #4d3a33 45%, #2c3a34 100%); box-shadow: 0 8px 18px rgba(0,0,0,0.18); }
  .rates-title { position: absolute; left: 262px; top: 296px; font-family: "Poppins", sans-serif; font-weight: 600; font-size: 20px; color: var(--ink); }
  .rates-text { position: absolute; left: 265px; top: 326px; font-size: 11px; color: var(--body-text); white-space: nowrap; }
  .booking-title { position: absolute; top: 466px; width: 100%; text-align: center; font-family: "Poppins", sans-serif; font-weight: 600; font-size: 21px; color: var(--ink); }
  .booking-intro { position: absolute; top: 502px; width: 100%; text-align: center; font-size: 12.4px; color: var(--body-text); }

  .contact-form .field { position: absolute; border: 2px solid var(--field-border); border-radius: 3px; background: var(--white); font-size: 11px; color: #333; text-transform: uppercase; padding: 12px 0 0 16px; }
  .submit-button { position: absolute; left: 474px; top: 810px; width: 108px; height: 37px; background: var(--brand-blue); color: var(--white); font-family: "Poppins", sans-serif; font-weight: 700; font-size: 16px; display: flex; align-items: center; justify-content: center; }

  /* Footer */
  .footer-art { position: absolute; left: 0; top: 860px; width: 1053px; height: 340px; }
  .site-footer .brand { left: 128px; top: 1046px; font-size: 25px; letter-spacing: 7px; gap: 16px; }
  .site-footer .brand-mark { background: var(--brand-blue); width: 16px; height: 16px; }
  .footer-divider { position: absolute; left: 536px; top: 1032px; width: 1px; height: 125px; background: var(--muted-line); }
  .footer-menu-title { position: absolute; left: 588px; top: 1047px; font-weight: 700; font-size: 11px; color: var(--white); }
  .footer-links { position: absolute; left: 588px; top: 1078px; font-size: 10px; color: var(--white); white-space: nowrap; word-spacing: 1px; }
  .footer-links span { margin: 0 7px; }
  .copyright { position: absolute; left: 589px; top: 1131px; font-size: 10px; color: var(--white); }
</style>
</head>
<body>
<div class="page">
  <header class="site-header">
    <div class="brand">
      <span class="brand-mark"></span>
      <span class="brand-name">Brightwater<br>Civic<br>Advisors</span>
    </div>
    <a class="cta-button" href="#book">BOOK A COMPLIMENTARY CONSULTATION</a>
    <nav class="main-nav">
      <a style="left:493px">ABOUT</a>
      <a style="left:562px">SERVICES &amp; TESTIMONIALS</a>
      <a style="left:739px">MEDIA &amp; IMPACT</a>
      <a class="is-current" style="left:867px">CONTACT</a>
    </nav>
  </header>

  <h1 class="page-title">Contact</h1>

  <div class="portrait" role="img" aria-label="Portrait photo of consultant Maren"></div>
  <h2 class="rates-title">Rates</h2>
  <p class="rates-text">Depending on the services requested, Maren offers an hourly rate, a package rate, or a retainer fee based on the scope and complexity of the project.</p>

  <h2 class="booking-title" id="book">Book a complimentary consultation</h2>
  <p class="booking-intro">Use the form below to tell Maren about your inquiry, and she will schedule a 30-minute meeting, phone call, or video chat to discuss your project outcomes.</p>

  <form class="contact-form">
    <div class="field" style="left:240px;top:556px;width:284px;height:39px">First Name</div>
    <div class="field" style="left:538px;top:556px;width:284px;height:39px">Last Name</div>
    <div class="field" style="left:240px;top:603px;width:284px;height:39px">Organization Name</div>
    <div class="field" style="left:538px;top:603px;width:284px;height:39px">Email Address</div>
    <div class="field" style="left:240px;top:651px;width:581px;height:39px">Subject</div>
    <div class="field" style="left:240px;top:698px;width:581px;height:88px">Message</div>
    <div class="submit-button">SUBMIT</div>
  </form>

  <footer class="site-footer">
    <svg class="footer-art" viewBox="0 0 1053 340" aria-hidden="false">
      <rect x="0" y="0" width="1053" height="160" fill="var(--band-light)" role="img" aria-label="Faint decorative pattern band"/>
      <rect x="0" y="0" width="1053" height="160" fill="url(#fade)"/>
      <defs>
        <linearGradient id="fade" x1="0" y1="0" x2="0" y2="1">
          <stop offset="0" stop-color="#ffffff" stop-opacity="0.6"/>
          <stop offset="1" stop-color="#ffffff" stop-opacity="0"/>
        </linearGradient>
      </defs>
      <polygon points="0,153 525,60 1053,154 1053,340 0,340" fill="var(--footer-dark)"/>
    </svg>
    <div class="brand">
      <span class="brand-mark"></span>
      <span class="brand-name">Brightwater<br>Civic<br>Advisors</span>
    </div>
    <div class="footer-divider"></div>
    <div class="footer-menu-title">MENU</div>
    <div class="footer-links">ABOUT<span>|</span>SERVICES &amp; TESTIMONIALS<span>|</span>MEDIA &amp; IMPACT<span>|</span>CONTACT</div>
    <div class="copyright">Copyrights @ 2019 All Rights Reserved</div>
  </footer>
</div>
</body>
</html>
```